Exciting & Elegant Stationary Pack

Stationary consists of
1. Letter head / Envelope
2. Business Card
3. Invoice
4. 40x40mm sticker

Attached files;

1. Logo (Other formats available on request)
2. MS word Doc - For information and description of design
3. Website image (This will be our new website so use the colours so everything ties together)
4. Sample of stationary pack we like, but feel free to be creative

Target Market(s)

Home improvement

Industry/Entity Type

Construction

Font styles to use
Other font styles liked:
• Leave up to designer - We like font used on (website attached image)

Requirements
Must have
• Please look at uploaded file of sample website and use colours
Nice to have
• Any type of business card design - eg. metal, die cut, embossed, etc...

```html
<!DOCTYPE html>
<html lang="en">
<head>
<meta charset="utf-8">
<title>Grout &amp; Level — Stationery Pack</title>
<link href="https://fonts.googleapis.com/css2?family=Lato:wght@400;700;900&display=swap" rel="stylesheet">
<style>
:root{
  --navy:#13466b;
  --orange:#f08a2c;
  --backdrop:#a9a7a8;
  --paper:#efeeec;
  --paper-white:#f7f7f6;
  --row:#cdd2da;
  --ink:#4a4f55;
  --accent-faint:#f3e3e3;
}
*{box-sizing:border-box;margin:0;padding:0}
html,body{width:1200px;height:838px;overflow:hidden;background:var(--backdrop);font-family:"Lato",Arial,sans-serif;color:var(--ink)}
.canvas{position:relative;width:1200px;height:838px}
.piece{position:absolute;box-shadow:1px 2px 4px rgba(0,0,0,.25);overflow:hidden}
.wordmark{font-family:"Lato",Arial,sans-serif;font-weight:900;color:var(--navy);letter-spacing:.5px;white-space:nowrap;position:absolute}
.wordmark.on-dark{color:#fff}

/* folder */
.folder{left:44px;top:50px;width:376px;height:530px;background:var(--navy)}
.folder .wordmark{right:34px;top:392px;font-size:27px}

/* shared footer band */
.footer-band{position:absolute;left:0;right:0;bottom:0;background:var(--navy);border-top:2px solid var(--orange);color:#fff;font-size:7px;display:flex;align-items:center;justify-content:center}
.footer-band::before{content:"";position:absolute;top:-2px;left:58px;border:5px solid transparent;border-top-color:var(--orange)}

/* letterhead */
.letterhead{left:435px;top:91px;width:347px;height:489px;background:var(--paper)}
.letterhead .wordmark{right:28px;top:30px;font-size:15px}
.letter-body{position:absolute;left:26px;top:137px;width:297px}
.salutation{font-size:9px;margin-bottom:21px}
.letter-body p{font-size:5px;line-height:8.4px;margin-bottom:8.4px;color:#555}
.letter-body p.salutation{font-size:9px;line-height:11px;margin-bottom:21px;color:var(--ink)}
.signoff{position:absolute;left:26px;top:343px;font-size:5px}
.signature{position:absolute;left:38px;top:355px;width:46px;height:12px;border-bottom:1px solid #444;background:none}
.signer{position:absolute;left:38px;top:380px;font-size:5.5px;line-height:9px}
.letterhead .footer-band{height:28px}

/* invoice */
.invoice{left:807px;top:94px;width:347px;height:490px;background:var(--paper)}
.invoice .wordmark{right:28px;top:30px;font-size:15px}
.inv-label{position:absolute;font-size:5.5px;font-weight:700;color:var(--navy)}
.inv-field{position:absolute;font-size:5.5px;display:flex;align-items:flex-end;gap:3px}
.inv-field span.line{flex:1;border-bottom:.8px solid #666;height:6px}
.inv-table{position:absolute;left:23px;top:153px;width:296px;height:241px;border:1px solid var(--navy);
  background:repeating-linear-gradient(180deg,#fff 0 13.4px,var(--row) 13.4px 26.8px);background-position:0 14px;background-repeat:repeat-y}
.inv-head{position:absolute;left:0;top:0;right:0;height:14px;background:var(--navy);color:#fff;font-size:5.5px;font-weight:700}
.inv-head span{position:absolute;top:4px}
.col-line{position:absolute;top:0;bottom:0;width:.8px;background:var(--navy)}
.pay-options{position:absolute;left:35px;top:400px;width:190px;display:flex;justify-content:space-between;font-size:5.5px}
.totals{position:absolute;left:241px;top:394px;width:78px;border:1px solid var(--navy);border-top:none}
.totals div{height:14px;display:flex;font-size:5.5px;font-weight:700;color:var(--navy);border-top:1px solid var(--navy)}
.totals div span:first-child{width:39px;border-right:1px solid var(--navy);padding:3px 0 0 3px}
.accept-note{position:absolute;left:23px;top:414px;font-size:4.6px;line-height:6.5px}
.invoice .footer-band{height:27px}

/* business cards */
.card-front{left:46px;top:594px;width:152px;height:87px;background:var(--paper-white)}
.card-front .wordmark{right:14px;top:12px;font-size:9px}
.card-front .card-band{position:absolute;left:0;right:0;bottom:0;height:37px;background:var(--navy);border-top:1.5px solid var(--orange)}
.card-band::before{content:"";position:absolute;top:-1.5px;left:26px;border:3px solid transparent;border-top-color:var(--orange)}
.card-name{position:absolute;left:13px;top:8px;font-size:5.5px;font-weight:700;color:var(--orange)}
.card-role{position:absolute;left:13px;top:16px;font-size:3.6px;color:#fff;font-weight:700}
.card-contact{position:absolute;right:13px;top:6px;font-size:3.6px;color:#fff;text-align:right;line-height:6px}
.card-back{left:42px;top:694px;width:152px;height:86px;background:var(--navy)}
.card-back .wordmark{right:8px;top:56px;font-size:9px}

/* envelopes */
.envelope-front{left:211px;top:603px;width:390px;height:177px;background:var(--paper-white)}
.envelope-front .wordmark{left:22px;top:22px;font-size:15px}
.envelope-art{position:absolute;left:65px;top:36px;width:112px;height:128px;background:var(--accent-faint);opacity:.8}
.envelope-front .footer-band{height:14px}
.envelope-front .footer-band::before{left:56px}
.envelope-back{left:614px;top:606px;width:392px;height:177px;background:var(--paper)}
.envelope-flap{position:absolute;left:0;top:0;right:0;height:57px;background:var(--navy);border-radius:0 0 12px 12px}
.envelope-flap .wordmark{left:50%;top:14px;transform:translateX(-50%);font-size:10px}

/* sticker */
.sticker{left:1025px;top:623px;width:157px;height:157px;background:#fff}
.sticker .wordmark{left:50%;top:66px;transform:translateX(-50%);font-size:17px}
</style>
</head>
<body>
<main class="canvas">

  <section class="piece folder">
    <span class="wordmark on-dark">GROUT &amp; LEVEL</span>
  </section>

  <section class="piece letterhead">
    <span class="wordmark">GROUT &amp; LEVEL</span>
    <div class="letter-body">
      <p class="salutation">Dear Mr. Carter,</p>
      <p>Thank you for choosing us for your bathroom renovation. We have reviewed the plans you sent last week and confirmed the tile selection, trims and adhesive with our supplier. Our team will arrive early on Monday morning to prepare the floor, set out levels and begin the waterproofing membrane. Please keep the room clear of furniture, towels and fittings, and let us know of any parking or access needs before we start so the first day runs smoothly and we can keep noise to a minimum for your neighbours.</p>
      <p>The work is expected to take five working days, including curing time for the membrane, adhesive and grout. We will protect the hallway floor with drop sheets, clean the site each afternoon and remove all offcuts and packaging when the job is finished. If we find any hidden damage behind the old tiles, such as rotten sheeting or a leaking pipe, we will stop, show you the problem and agree on a price before any extra work goes ahead.</p>
      <p>All materials are covered by the manufacturer warranty and our workmanship is guaranteed for seven years from the date of completion. If you notice any cracked tile, loose trim, drummy sound or staining in that time, call us and we will come back to inspect and repair it at no cost to you. We also offer sealing and maintenance visits on request, which help keep grout lines clean and water tight. Many of our clients book a check every two years, and we are happy to send a reminder when yours is due.</p>
      <p>A copy of the quote, the product list and the payment schedule is attached for your records. Feel free to contact me directly with any questions about the project, the timing or the finishes, and I will get back to you the same day.</p>
    </div>
    <p class="signoff">Sincerely,</p>
    <div class="signature" role="img" aria-label="Handwritten signature"></div>
    <p class="signer">Owen Hartley<br>CEO/ Founder</p>
    <footer class="footer-band">0400 555 123 | info@groutandlevel.com.au | www.groutandlevel.com.au</footer>
  </section>

  <section class="piece invoice">
    <span class="wordmark">GROUT &amp; LEVEL</span>
    <span class="inv-label" style="left:26px;top:104px">INVOICE # :</span>
    <span class="inv-label" style="left:246px;top:104px">DATE :</span>
    <div class="inv-field" style="left:24px;top:116px;width:295px">Customer: <span class="line"></span></div>
    <div class="inv-field" style="left:24px;top:128px;width:295px">Address : <span class="line"></span></div>
    <div class="inv-field" style="left:24px;top:140px;width:148px">Phone : <span class="line"></span></div>
    <div class="inv-field" style="left:180px;top:140px;width:139px">Fax : <span class="line"></span></div>
    <div class="inv-table">
      <div class="inv-head">
        <span style="left:6px">QTY</span>
        <span style="left:95px">DESCRIPTION</span>
        <span style="left:225px">PRICE</span>
        <span style="left:262px">AMOUNT</span>
      </div>
      <i class="col-line" style="left:25px"></i>
      <i class="col-line" style="left:218px"></i>
      <i class="col-line" style="left:257px"></i>
    </div>
    <div class="pay-options"><span>CREDIT</span><span>EFT</span><span>DEBIT</span><span>CASH</span><span>CHEQUE</span></div>
    <div class="totals">
      <div><span>SUB TOTAL</span><span></span></div>
      <div><span>GST #</span><span></span></div>
      <div><span>SUBTOTAL</span><span></span></div>
    </div>
    <p class="accept-note">Signature Indicates<br>Acceptance of Price and term</p>
    <footer class="footer-band">0400 555 123 | info@groutandlevel.com.au | www.groutandlevel.com.au</footer>
  </section>

  <section class="piece card-front">
    <span class="wordmark">GROUT &amp; LEVEL</span>
    <div class="card-band">
      <span class="card-name">DANA WHITFIELD</span>
      <span class="card-role">PROJECT MANAGER</span>
      <p class="card-contact">P. 0400 555 123<br>INFO@GROUTANDLEVEL.COM.AU<br>WWW.GROUTANDLEVEL.COM.AU<br>LIC NO. 204118C</p>
    </div>
  </section>

  <section class="piece card-back">
    <span class="wordmark on-dark">GROUT &amp; LEVEL</span>
  </section>

  <section class="piece envelope-front">
    <div class="envelope-art" role="img" aria-label="Faint lighthouse illustration"></div>
    <span class="wordmark">GROUT &amp; LEVEL</span>
    <footer class="footer-band"></footer>
  </section>

  <section class="piece envelope-back">
    <div class="envelope-flap">
      <span class="wordmark on-dark">GROUT &amp; LEVEL</span>
    </div>
  </section>

  <section class="piece sticker">
    <span class="wordmark">GROUT &amp; LEVEL</span>
  </section>

</main>
</body>
</html>
```